first fantastic look and impression

We are looking for a concept for letterhead, business card, emailfooter and template for invoices or offers for our company in the consultation business.
The dancer is a symbol who we are: it looks simple, but there is a lot of hard work and many years of training in this movement. The look is also what we want: elegant, modern, strong, with a touch of extravaganza
Target Market(s)
Hotelbusiness , Consulting
Font styles to use
Sans Serif
Other font styles liked:
- please give us a option we are open
Requirements
Must have
- We are not typical consultants but sparring partners and coaches for the hotel and that should also be expressed in the design. Maybe there is an icon that supports the whole thing. We are more modern and bolder than our industry colleagues.
we are modern, fresh, agile, fast
Nice to have
- a icon

```html
<!DOCTYPE html>
<html lang="en">
<head>
<meta charset="utf-8">
<title>Halden Consulting – Business Card</title>
<link rel="stylesheet" href="https://fonts.googleapis.com/css2?family=Montserrat:wght@500;700&family=Roboto:wght@400&display=swap">
<style>
  :root {
    --backdrop: #979797;
    --card-white: #f7f7f6;
    --card-black: #1c1d1f;
    --ink-navy: #1f2231;
    --ink-grey: #5d5f66;
    --silver: #b9babd;
  }
  * { margin: 0; padding: 0; box-sizing: border-box; }
  html, body {
    width: 1200px;
    height: 1113px;
    overflow: hidden;
    background: var(--backdrop);
  }
  .canvas {
    position: relative;
    width: 1200px;
    height: 1113px;
  }
  .card {
    position: absolute;
    width: 700px;
    height: 400px;
    border-radius: 3px;
  }
  .card--front {
    left: 130px;
    top: 120px;
    background: var(--card-white);
  }
  .card--back {
    left: 370px;
    top: 590px;
    background: var(--card-black);
    display: flex;
    align-items: center;
    justify-content: center;
  }
  .contact {
    position: absolute;
    left: 56px;
    top: 190px;
    color: var(--ink-grey);
    font-family: "Roboto", sans-serif;
  }
  .contact__name {
    font-family: "Montserrat", sans-serif;
    font-weight: 700;
    font-size: 20px;
    color: var(--ink-navy);
    letter-spacing: -0.2px;
  }
  .contact__role {
    font-family: "Montserrat", sans-serif;
    font-weight: 500;
    font-size: 17px;
    margin-bottom: 14px;
  }
  .contact__line {
    display: flex;
    align-items: center;
    gap: 10px;
    font-size: 17px;
    line-height: 24px;
  }
  .contact__icon {
    width: 16px;
    height: 16px;
    flex: none;
  }
  .wordmark {
    font-family: "Montserrat", sans-serif;
    font-weight: 500;
    display: flex;
    align-items: center;
    gap: 12px;
  }
  .wordmark__dot {
    width: 12px;
    height: 12px;
    border-radius: 50%;
    background: currentColor;
  }
  .card--front .wordmark {
    position: absolute;
    right: 56px;
    top: 148px;
    font-size: 22px;
    color: var(--ink-navy);
  }
  .card--back .wordmark {
    font-size: 34px;
    color: var(--silver);
  }
</style>
</head>
<body>
<main class="canvas">
  <section class="card card--front" aria-label="Business card front">
    <div class="contact">
      <p class="contact__name">ELENA MARWICK</p>
      <p class="contact__role">Managing Director</p>
      <p class="contact__line">
        <svg class="contact__icon" viewBox="0 0 16 16" aria-hidden="true"><path fill="var(--ink-navy)" d="M3 1h3l1 4-2 1.5c.8 1.8 2 3 3.5 3.5L10 8l4 1v3c0 1-1 2-2 2C6.5 14 2 9.5 2 3c0-1 .5-2 1-2z"/></svg>
        +56912470385
      </p>
      <p class="contact__line">
        <svg class="contact__icon" viewBox="0 0 16 16" aria-hidden="true"><rect x="1" y="3" width="14" height="10" fill="var(--ink-navy)"/><path d="M1.5 3.5 8 9l6.5-5.5" fill="none" stroke="var(--card-white)" stroke-width="1.2"/></svg>
        info@haldenconsulting.com
      </p>
      <p class="contact__line">
        <svg class="contact__icon" viewBox="0 0 16 16" aria-hidden="true"><g fill="none" stroke="var(--ink-navy)" stroke-width="1.3"><circle cx="8" cy="8" r="6.5"/><ellipse cx="8" cy="8" rx="3" ry="6.5"/><path d="M1.5 8h13"/></g></svg>
        www.haldenconsulting.com
      </p>
    </div>
    <div class="wordmark"><span class="wordmark__dot"></span>Halden Consulting</div>
  </section>

  <section class="card card--back" aria-label="Business card back">
    <div class="wordmark"><span class="wordmark__dot"></span>Halden Consulting</div>
  </section>
</main>
</body>
</html>
```